Dentistry Office

We want a new design for a Dentist's office website.

The theme is: "We provide high quality, state-of-the-art, dental care in a comfortable, caring environment."

The site currently has a menu on the left of the page with about 40 items on it. There is a great deal of textual content on each page, plus several illustrations.

We want to do this using CSS, so we need specifications in the CSS for all possible elements. The CSS needs to be named in a logical manner for easy use.

Every dentist on the planet seems to use lots of Flash. We don't want to because it is so distracting. We are looking for an elegant solution targeting 24-55 age group, but not excluding anyone.

The following (from another dentist's site) can give you a taste of what we want to communicate on the site:

"After 20 years of teaching dentists how to refine their technique and many years of writing textbooks, I currently devote my time to my office and the hands-on practice of dentistry. I'd like to welcome you personally to my dental practice, and I invite you to meet my highly experienced team of professionals.

"We have offered complete dental care of the highest quality since 1978. We provide Preventive Services, Tooth Whitening and Cosmetic Dentistry for a beautiful smile, Endodontics (root canal treatment) to treat painful teeth, Sedation Dentistry so you can relax, and Dental Implants to restore what is missing. We offer total care.

"Our approach to your health is simple: We use our education, experience and dedication to provide every patient with superior dental care.

"This passion for excellence is not just a goal, but a standard every member of our team holds.

"We also pride ourselves with our state of the art procedures, training and technology. This includes creating a beautiful smile using techniques that preserve as much of the original tooth as possible.

"Our abilities are renowned throughout the dental profession and I hope if you have any questions you will contact us by an e-mail note, by phone or just by dropping by."

Keep in mind the screen shape and dimensions. Your design needs to work in the normal screen proportions, regardless of how it looks when you post it here. Scrolling is OK, but the first impression needs to work.
Updates

Keep in mind that there will be about 250 words, or more, on each page.

Competitors web sites:

http://www.brindlecovedentist.example/

http://www.brindlecovedentalcare.example/

http://www.grinsbymarlowvaledental.example/

http://www.tenbyfamilydentalcare.example/

http://www.quelmardental.example/

http://www.dovrinadental.example/

We need to compete with these.

Target Market(s)

Generally adults seeking the most experienced and comfortable-to-be-with dentist.

Industry/Entity Type

Training

Requirements
Must have
• Must stand apart from other dentists.
• Must be elegant.
• Must have a horizontal menu structure across all columns, NOT a vertical that requires scrolling, no popout, pop down, etc. menus.
• We are looking for something special.
• Do not waste your time or ours putting up templates and things you have used before.
• Personally, I do not see how someone outside the US can understand the northern California dental market. But you are welcome to try.
Should not have
• Flash or graphics that move
• The look of a template
• Folksy fonts
• Looks like you used it 20 times before

```html
<!DOCTYPE html>
<html lang="en">
<head>
<meta charset="utf-8">
<title>Calder Springs Dentist</title>
<link rel="stylesheet" href="https://fonts.googleapis.com/css2?family=Arimo:wght@400;700&display=swap">
<style>
  :root {
    --brand: #2b6483;
    --brand-dark: #2f6a88;
    --brand-light: #5d8ea6;
    --ink: #222;
    --body-text: #555;
    --heading-text: #444;
    --rule: #dcdfe1;
    --tab-bg: #e5e7e8;
    --menu-bg: #e2e9ed;
    --canvas: #eef0f1;
    --white: #fff;
  }
  * { box-sizing: border-box; margin: 0; padding: 0; }
  html, body { width: 1200px; height: 900px; overflow: hidden; }
  body { background: var(--canvas); font-family: "Arimo", Helvetica, Arial, sans-serif; color: var(--body-text); position: relative; }
  .page { position: absolute; left: 182px; top: 0; width: 843px; height: 900px; background: var(--white); border-left: 1px solid #cfd3d5; border-right: 1px solid #cfd3d5; }
  .abs { position: absolute; }

  .site-name { left: 254px; top: 70px; font-size: 20px; font-weight: 700; color: var(--brand); }
  .site-name-mark { left: 222px; top: 72px; width: 20px; height: 20px; border: 2px solid #8a9399; border-radius: 50%; }
  .header-rule { left: 213px; top: 105px; width: 780px; height: 1px; background: var(--rule); }

  .search { left: 837px; top: 81px; display: flex; height: 16px; }
  .search-field { width: 107px; border: 1px solid #cfd3d5; background: #f3f4f5; font-size: 9px; color: #999; padding: 3px 8px 0; }
  .search-button { width: 49px; background: var(--brand-dark); color: var(--white); font-size: 10px; text-align: center; line-height: 15px; }

  .main-nav { left: 221px; top: 129px; display: flex; gap: 8px; }
  .main-nav a { height: 26px; line-height: 27px; padding: 0 7px; font-size: 12.5px; color: var(--ink); background: var(--tab-bg); text-decoration: none; white-space: nowrap; }
  .main-nav a.is-active { background: var(--brand-dark); color: var(--white); padding: 0 16px; }

  .nav-band { left: 213px; top: 155px; width: 780px; height: 31px; background: linear-gradient(90deg, #2f6986, #3f7792); }
  .content-sheet { left: 213px; top: 186px; width: 592px; height: 200px; background: var(--white); box-shadow: 2px 0 3px rgba(0,0,0,.15); }
  .tools-panel { left: 805px; top: 186px; width: 188px; height: 100px; background: linear-gradient(180deg, #3b7390, #7aa1b5); }
  .tools-panel ul { list-style: none; padding: 31px 0 0 12px; }
  .tools-panel li { display: flex; align-items: center; gap: 8px; color: var(--white); font-size: 10px; height: 18px; }

  .page-title { left: 221px; top: 233px; font-size: 19.5px; font-weight: 400; color: var(--heading-text); line-height: 22px; white-space: nowrap; }
  .lead { left: 221px; top: 296px; width: 550px; font-size: 14px; color: var(--brand-dark); line-height: 24.5px; }
  .lead span { border-bottom: 1px solid #c9d6dd; padding-bottom: 3px; }

  .column { font-size: 10.1px; line-height: 18.1px; color: var(--body-text); }
  .column h2 { font-size: 10.1px; font-weight: 700; color: var(--ink); margin-bottom: 1px; }
  .column p + h2 { margin-top: 18px; }
  .col-left { left: 221px; top: 378px; width: 284px; }
  .col-right { left: 517px; top: 375px; width: 282px; }
  .col-right-end { left: 517px; top: 664px; width: 284px; }

  .diagram { left: 527px; top: 470px; width: 263px; height: 190px; background: radial-gradient(ellipse at 30% 55%, #d9869a 0 25%, #f1c9d3 45%, transparent 62%), radial-gradient(ellipse at 78% 55%, #efd1c2 0 22%, transparent 45%), #fbf8f7; }
  .smile-photo { left: 813px; top: 291px; width: 180px; height: 81px; background: linear-gradient(100deg, #f4ece9 0%, #d9a39a 45%, #b07065 70%, #e9d7d2 100%); }

  .side-menu { left: 813px; top: 385px; width: 180px; list-style: none; }
  .side-menu li { height: 24.6px; display: flex; align-items: center; gap: 10px; padding-left: 14px; font-size: 12px; border-bottom: 1px solid var(--white); }
  .side-menu .menu-section { background: var(--menu-bg); color: var(--brand-dark); border-bottom: 2px solid #cfd9de; }
  .side-menu .menu-item { background: var(--white); color: #555; font-size: 10.5px; border-bottom: 1px solid var(--rule); }
  .side-menu svg { flex: none; }

  .emergency { left: 813px; top: 648px; width: 180px; height: 112px; border: 1px solid #d3d8db; background: linear-gradient(180deg, #fff, #dfe3e6); }
  .emergency svg { position: absolute; left: 20px; top: 32px; }
  .emergency-label { position: absolute; left: 49px; top: 32px; font-size: 14px; font-weight: 700; color: var(--brand-dark); letter-spacing: 1.4px; }
  .emergency-number { position: absolute; left: 49px; top: 59px; font-size: 13px; font-weight: 700; color: #333; }

  .footer-rule { left: 213px; top: 804px; width: 780px; height: 1px; background: var(--rule); }
  .footer-col { top: 818px; font-size: 10px; line-height: 15px; color: #555; }
  .footer-col h3 { font-size: 12px; font-weight: 400; color: var(--brand-dark); margin-bottom: 5px; }
  .footer-contact { left: 813px; top: 826px; font-size: 10px; line-height: 15px; color: #555; }
  .footer-contact b { color: var(--brand-dark); font-weight: 400; }
  .footer-contact .email { color: var(--brand-dark); }
</style>
</head>
<body>
  <div class="page"></div>

  <span class="abs site-name-mark"></span>
  <div class="abs site-name">Calder Springs Dentist</div>
  <div class="abs search"><div class="search-field">Enter your search text</div><div class="search-button">search</div></div>
  <div class="abs header-rule"></div>

  <nav class="abs main-nav">
    <a class="is-active" href="#">Home</a>
    <a href="#">Why we are different</a>
    <a href="#">Technologies we offer</a>
    <a href="#">Meet Dr. Hendry</a>
    <a href="#">Our Staff</a>
    <a href="#">Contact us</a>
  </nav>

  <div class="abs nav-band"></div>
  <div class="abs tools-panel">
    <ul>
      <li><svg width="12" height="10" viewBox="0 0 12 10"><rect x="3" y="0" width="6" height="3" fill="#fff"/><rect x="0" y="3" width="12" height="5" rx="1" fill="#fff"/><rect x="3" y="6" width="6" height="4" fill="#fff" stroke="#3b7390"/></svg>print this page</li>
      <li><svg width="12" height="9" viewBox="0 0 12 9"><rect x="0" y="0" width="12" height="9" fill="#fff"/><path d="M0 0 L6 5 L12 0" fill="none" stroke="#3b7390"/></svg>e-mail this page</li>
    </ul>
  </div>
  <div class="abs content-sheet"></div>

  <h1 class="abs page-title">Providing Cosmetic Dentistry Excellence to Patients in<br>Calder Springs, Wren County and the San Francisco Bay Area</h1>
  <p class="abs lead"><span>In Calder Springs, when you’re a patient of Dr. Hendry, you can be confident that you’re receiving care from the most experienced, knowledgeable, and skilled cosmetic dentist in Wren County.</span></p>

  <div class="abs column col-left">
    <h2>Award-winning leader in restorative dentistry</h2>
    <p>Dr. Hendry is an award-winning leader in restorative dentistry and a genial professional. His humor, dedication, and talent ensure you a pleasant experience and superb, long-lasting results. After 25 years of teaching dentists how to refine their technique and many years of writing textbooks, I currently devote my time to my office and the hands-on practice of dentistry. I’d like to welcome you personally to my dental practice, and I invite you to meet my highly experienced team of professionals. Dr. Hendry is an award-winning leader in restorative dentistry and a genial professional. His humor, dedication, and talent ensure you a pleasant experience and superb, long-lasting results.</p>
    <h2>25 years of teaching</h2>
    <p>After 25 years of teaching dentists how to refine their tech-nique and many years of writing textbooks, I currently devote my time to my office and the hands-on practice of dentistry. I’d like to welcome you personally to my dental practice, and I invite you to meet my highly experienced team of profession-als lorem vestibulum in massa ac ipsum pharetra faucibus. After 25 years of teaching dentists how to refine their tech-</p>
  </div>

  <div class="abs column col-right">
    <h2>Our approach to your health</h2>
    <p>Our approach to your health is simple: We use our education, experience and dedication to provide every patient with supe-rior dental care.</p>
    <p>This passion for excellence is not just a goal, but a</p>
  </div>
  <div class="abs diagram" role="img" aria-label="Illustration of the oral cavity and a chart of permanent teeth"></div>
  <div class="abs column col-right-end">
    <p>standard every member of our team holds.<br>We also pride ourselves with our state of the art procedures, training and technology. This includes creating a beautiful smile using techniques that preserve as much of the original tooth as possible. Our abilities are renowned throughout the dental profession and I hope if you have any questions you will contact us by an e-mail note, by phone or just by dropping by.</p>
  </div>

  <div class="abs smile-photo" role="img" aria-label="Photo of a smiling patient wearing clear braces"></div>

  <ul class="abs side-menu">
    <li class="menu-section"><svg width="7" height="6" viewBox="0 0 7 6"><path d="M0 0H7L3.5 6Z" fill="#2f6a88"/></svg>Education</li>
    <li class="menu-item"><svg width="5" height="6" viewBox="0 0 5 6"><path d="M0 0L5 3L0 6Z" fill="#555"/></svg>Emergency Dental Care</li>
    <li class="menu-item"><svg width="5" height="6" viewBox="0 0 5 6"><path d="M0 0L5 3L0 6Z" fill="#555"/></svg>Your Mouth</li>
    <li class="menu-item"><svg width="5" height="6" viewBox="0 0 5 6"><path d="M0 0L5 3L0 6Z" fill="#555"/></svg>Your Tooth</li>
    <li class="menu-item"><svg width="5" height="6" viewBox="0 0 5 6"><path d="M0 0L5 3L0 6Z" fill="#555"/></svg>Cracked Tooth?</li>
    <li class="menu-section"><svg width="6" height="7" viewBox="0 0 6 7"><path d="M0 0L6 3.5L0 7Z" fill="#2f6a88"/></svg>Preventative</li>
    <li class="menu-section"><svg width="6" height="7" viewBox="0 0 6 7"><path d="M0 0L6 3.5L0 7Z" fill="#2f6a88"/></svg>Education</li>
    <li class="menu-section"><svg width="6" height="7" viewBox="0 0 6 7"><path d="M0 0L6 3.5L0 7Z" fill="#2f6a88"/></svg>Cosmetics</li>
    <li class="menu-section"><svg width="6" height="7" viewBox="0 0 6 7"><path d="M0 0L6 3.5L0 7Z" fill="#2f6a88"/></svg>Restorations</li>
    <li class="menu-section"><svg width="6" height="7" viewBox="0 0 6 7"><path d="M0 0L6 3.5L0 7Z" fill="#2f6a88"/></svg>Visiting our office</li>
  </ul>

  <div class="abs emergency">
    <svg width="20" height="42" viewBox="0 0 20 42"><path d="M9 2 C2 6 0 14 0 21 C0 28 2 36 9 40 L13 36 C8 32 7 26 7 21 C7 16 8 10 13 6 Z" fill="#2f6a88"/><rect x="11" y="1" width="7" height="8" rx="2" fill="#2f6a88"/><rect x="11" y="33" width="7" height="8" rx="2" fill="#2f6a88"/></svg>
    <div class="emergency-label">Emergency</div>
    <div class="emergency-number">(555) 292-5908</div>
  </div>

  <div class="abs footer-rule"></div>
  <div class="abs footer-col" style="left:213px"><h3>About Owen Hendry</h3>lorem ipsum dolar sit<br>lorem ipsum dolar sit<br>lorem ipsum dolar sit</div>
  <div class="abs footer-col" style="left:410px"><h3>Technologies we offer</h3>lorem ipsum dolar sit<br>lorem ipsum dolar sit<br>lorem ipsum dolar sit</div>
  <div class="abs footer-col" style="left:607px"><h3>Address</h3>1100 Wren Avenue<br>Calder Springs</div>
  <div class="abs footer-contact"><b>T</b> (555) 575-1190<br><b>F</b> 0100 457 893<br><span class="email">drhendry@hendrydental.example</span></div>
</body>
</html>
```